ELsewhen website redesign to provide information about experiential workshops, film work and other

We need a redesign of our website elsewhen.org. We conduct experiential workshops of discovery and transformation for individuals and organizations. We need the website to reflect the full extent of ELsewhen programs, and be an information hub for ELsewhen workshops and communities as they develop.

The attached documents contain information about the organization - it's brandbook, copy for web pages, a website layout and a couple of images.

The site is for individuals and companies looking to promote and be change to make a difference. It should be warm, welcoming, and create excitement around the concepts and the ability to discover a new way of being in the world. We are about creating communities around the globe who will embody play, freedom, curiosity and expanded possibilities. We are creating a space for this to happen, both physically (workshops) and online.

We will be on either a SquareSpace, but mos tlikely a Weebly plaform.

Please look at the current site at www.elsewhen.org

Target Market(s)

Initially, are target market will be baby boomers, but will expand to include millennials and students.

Coding

Coded - Design and coding required

Number of Pages Required

5+ page

Requirements
Must have
• The colors, logo and fonts from the brand book.
Nice to have
• Complimentary use of brand colors to create an attractive presentation and energy

```html
<!DOCTYPE html>
<html lang="en">
<head>
<meta charset="utf-8">
<title>ELsewhen</title>
<link href="https://fonts.googleapis.com/css2?family=Jost:wght@300;400;500;600;700&family=Open+Sans:wght@400;600&display=swap" rel="stylesheet">
<style>
:root{
  --orange:#f05a28;
  --orange-warm:#f2a33a;
  --orange-deep:#f26532;
  --blush:#f4c3b6;
  --ink:#1d1d1d;
  --text:#6b6b6b;
  --green:#7dbb80;
  --footer:#1c1c1c;
  --footer-base:#121212;
  --white:#ffffff;
}
*{margin:0;padding:0;box-sizing:border-box}
html,body{width:1200px;height:3409px;overflow:hidden}
body{position:relative;font-family:"Open Sans",Arial,sans-serif;color:var(--text);background:var(--white)}
.abs{position:absolute}
.heading{font-family:"Jost",Arial,sans-serif}

/* Hero */
.hero{position:absolute;left:0;top:0;width:1200px;height:648px;background:linear-gradient(160deg,#3a3a3a 0%,#2a2723 45%,#1e1d1b 100%)}
.brand{font-family:"Jost",Arial,sans-serif;font-weight:600;color:var(--white);font-size:31px;letter-spacing:4px;display:flex;align-items:center;gap:12px}
.brand-mark{width:26px;height:26px;background:var(--white)}
.hero .brand{left:183px;top:48px}
.member-login{left:818px;top:50px;width:128px;height:32px;border:1.5px solid var(--white);border-radius:16px;color:var(--white);font-family:"Jost",sans-serif;font-size:12px;font-weight:500;display:flex;align-items:center;justify-content:center}
.menu{left:968px;top:55px;width:32px}
.menu span{display:block;height:2px;background:var(--white);margin-bottom:7px}
.hero-question{color:var(--white);font-family:"Jost",sans-serif;font-weight:600;font-size:30px;line-height:38px;text-transform:uppercase;width:380px}
.hero-question::before{content:"";display:block;width:44px;height:5px;background:var(--white);margin-bottom:12px}
.signup{left:464px;top:416px;width:206px;height:54px;border-radius:27px;background:var(--orange);color:var(--white);font-family:"Jost",sans-serif;font-weight:600;font-size:19px;display:flex;align-items:center;justify-content:center;text-transform:uppercase}

/* Discover */
.discover-title{left:0;top:712px;width:1200px;text-align:center;color:var(--ink);font-weight:700;font-size:24px;line-height:32px;text-transform:uppercase;letter-spacing:.5px}
.benefit{width:190px;text-align:center;top:826px}
.benefit svg{display:block;margin:0 auto 14px}
.benefit p{font-family:"Jost",sans-serif;color:var(--orange);font-weight:600;font-size:12px;line-height:16px;text-transform:uppercase}

/* Vision */
.vision{left:0;top:1039px;width:1200px;height:452px;background:linear-gradient(90deg,#7d7570 0%,#a08c86 35%,#d9a89c 55%,var(--blush) 75%,#f6cabd 100%)}
.vision h2{left:652px;top:82px;color:var(--white);font-size:32px;font-weight:600;text-transform:uppercase}
.vision p{left:652px;top:135px;width:440px;color:var(--white);font-size:14.5px;line-height:22.5px}

/* What we do */
.section-title{left:0;top:1578px;width:1200px;text-align:center;color:var(--ink);font-weight:700;font-size:27px;text-transform:uppercase}
.program-title{left:0;top:1652px;width:1200px;text-align:center;color:#333;font-weight:300;font-size:30px}
.program-text{left:180px;top:1700px;width:840px;text-align:center;font-size:13.5px;line-height:24px;color:var(--text)}
.program-sub{left:0;top:1818px;width:1200px;text-align:center;color:var(--orange);font-family:"Jost",sans-serif;font-size:21px;line-height:30px}
.movement{top:1912px;width:160px;text-align:center}
.movement svg{display:block;margin:0 auto 10px}
.movement p{font-family:"Jost",sans-serif;font-size:16px;color:#555}

/* Shaking the Still */
.still{left:0;top:2091px;width:1200px;height:473px;background:linear-gradient(90deg,var(--orange-warm) 0%,#f38a36 50%,var(--orange-deep) 100%)}
.still h2{left:556px;top:80px;color:var(--white);font-weight:300;font-size:30px}
.still p{left:556px;width:540px;color:var(--white);font-size:14.5px;line-height:23px}

/* Community */
.community{left:0;top:2564px;width:1200px;height:482px;background:linear-gradient(90deg,#f2f2f2 0%,#e9e9e9 45%,#dcdcdc 75%,#cfcfcf 100%)}
.community h2{left:177px;top:134px;color:#333;font-weight:400;font-size:26px}
.community p{left:177px;top:183px;width:320px;font-size:17px;line-height:26px;color:#777}
.contact-form{left:532px;top:57px;width:484px;height:329px;background:var(--green);padding:38px 38px 0}
.field{background:var(--white);height:31px;margin-bottom:11px;font-size:12px;color:#444;padding:7px 14px}
.field.message{height:92px}
.send{margin-top:18px;width:112px;height:33px;border-radius:17px;background:#111;color:var(--white);font-family:"Jost",sans-serif;font-size:13px;font-weight:500;display:flex;align-items:center;justify-content:center;text-transform:uppercase}

/* Footer */
.footer{left:0;top:3046px;width:1200px;height:291px;background:var(--footer)}
.footer .brand{left:183px;top:79px;font-size:22px;letter-spacing:3px}
.footer .brand-mark{width:18px;height:18px}
.footer-col{top:85px}
.footer-col h3{font-family:"Jost",sans-serif;color:var(--white);font-weight:500;font-size:16px;text-transform:uppercase;margin-bottom:22px}
.footer-col a{display:block;color:#ddd;font-family:"Jost",sans-serif;font-size:14px;text-decoration:none;margin-bottom:14px}
.social{display:flex;gap:20px}
.social span{width:18px;height:18px;border-radius:50%;background:var(--white)}
.base{left:0;top:3337px;width:1200px;height:72px;background:var(--footer-base);color:#888;font-size:11px;display:flex;align-items:center;justify-content:center}
</style>
</head>
<body>

<header class="hero" role="img" aria-label="Photo of workshop participants seated in a circle in a dim room">
  <div class="abs brand"><span class="brand-mark"></span>ELSEWHEN</div>
  <div class="abs member-login">MEMBER LOGIN</div>
  <div class="abs menu"><span></span><span></span><span></span></div>
  <h1 class="abs hero-question" style="left:175px;top:280px">What world do we want to live in?</h1>
  <h1 class="abs hero-question" style="left:686px;top:280px">What kind of life do you want to create?</h1>
  <a class="abs signup">Sign up email</a>
</header>

<h2 class="abs heading discover-title">Discover an opportunity to live a more<br>dynamic and meaningful life</h2>

<div class="abs benefit" style="left:128px">
  <svg width="56" height="60" viewBox="0 0 56 60" fill="none" stroke="#f05a28" stroke-width="2"><circle cx="28" cy="26" r="13"/><path d="M22 39v8h12v-8M23 52h10M28 4v5M8 26h-5M53 26h-5M13 11l4 4M43 11l-4 4"/></svg>
  <p>Moves<br>energy</p>
</div>
<div class="abs benefit" style="left:291px">
  <svg width="56" height="60" viewBox="0 0 56 60" fill="none" stroke="#f05a28" stroke-width="2"><rect x="10" y="6" width="36" height="48"/><path d="M10 6l14 6v46l-14-4M32 30h2M46 6l-14 6v46l14-4"/></svg>
  <p>Creates opportunities<br>for connecting</p>
</div>
<div class="abs benefit" style="left:475px">
  <svg width="56" height="60" viewBox="0 0 56 60" fill="none" stroke="#f05a28" stroke-width="2"><circle cx="28" cy="14" r="8"/><circle cx="28" cy="14" r="3"/><path d="M12 54v-10a8 8 0 0 1 16 0v10M28 54v-10a8 8 0 0 1 16 0v10M10 54h36"/></svg>
  <p>Supports<br>conscious evolution</p>
</div>
<div class="abs benefit" style="left:678px">
  <svg width="56" height="60" viewBox="0 0 56 60" fill="none" stroke="#f05a28" stroke-width="2"><path d="M8 54h40M14 54V36h10v18M24 54V28h10v26M34 54V20h10v34M36 12l12-8M44 4h4v4"/></svg>
  <p>Deepens<br>experience of life</p>
</div>
<div class="abs benefit" style="left:832px">
  <svg width="56" height="60" viewBox="0 0 56 60" fill="none" stroke="#f05a28" stroke-width="2"><circle cx="28" cy="28" r="22"/><ellipse cx="28" cy="28" rx="10" ry="22"/><path d="M6 28h44M10 16h36M10 40h36"/></svg>
  <p>Provides opportunities<br>for collaboration<br>and creation</p>
</div>

<section class="abs vision" role="img" aria-label="Photo of two women in conversation on a workshop stage, fading into blush pink">
  <h2 class="abs heading">Vision</h2>
  <p class="abs">We envision a world in which all people and communities can challenge and break free from stories that no longer serve us. We believe that solutions to contemporary challenges will emerge from a place of curiosity, love and connection. Through inspiration, conscious reflection, and collaboration, we take responsibility for the world we are manifesting, and we can discover and create new possibilities for the lives and the society we desire to build.</p>
</section>

<h2 class="abs heading section-title">What we do</h2>
<h3 class="abs heading program-title">ELsewhen Life</h3>
<p class="abs program-text">ELsewhen Life is a workshop designed to re-engage you with life. Through interactive exercises and personal exploration, you are taken on a journey that ultimately leaves you experiencing life as a Creator. You will learn to see beliefs and patterns that hold you back in work and relationships as well as a path to transforming the story of your life.</p>
<p class="abs program-sub">ELsewhen Life  is a 2-3 day workshop<br>experienced in 5 movements:</p>

<div class="abs movement" style="left:231px">
  <svg width="72" height="72" viewBox="0 0 72 72" fill="none" stroke="#f05a28" stroke-width="2.5"><circle cx="36" cy="36" r="33"/></svg>
  <p>Curiosity</p>
</div>
<div class="abs movement" style="left:363px">
  <svg width="72" height="72" viewBox="0 0 72 72" fill="none" stroke="#f05a28" stroke-width="2.5"><path d="M36 6L68 66H4Z M36 6V66"/></svg>
  <p>Awareness</p>
</div>
<div class="abs movement" style="left:488px">
  <svg width="72" height="72" viewBox="0 0 72 72" fill="none" stroke="#f05a28" stroke-width="2.5"><path d="M4 20L68 52V20L4 52Z"/></svg>
  <p>Owning Your Creation</p>
</div>
<div class="abs movement" style="left:686px">
  <svg width="72" height="72" viewBox="0 0 72 72" fill="none" stroke="#f05a28" stroke-width="2.5"><path d="M36 4V68M14 14l44 44M58 14L14 58"/></svg>
  <p>Reimagining</p>
</div>
<div class="abs movement" style="left:831px">
  <svg width="72" height="72" viewBox="0 0 72 72" fill="none" stroke="#f05a28" stroke-width="2.5"><path d="M36 6L68 66H4Z M36 6V66M14 48h44"/></svg>
  <p>Manifesting</p>
</div>

<section class="abs still">
  <svg class="abs" style="left:136px;top:34px" width="390" height="400" viewBox="0 0 390 400">
    <polygon points="97,8 293,8 386,200 293,392 97,392 4,200" fill="none" stroke="#fff" stroke-width="2.5"/>
    <polygon points="107,24 283,24 367,200 283,376 107,376 23,200" fill="#8a6b4e" role="img" aria-label="Photo of workshop participants sitting together on a patterned rug"/>
  </svg>
  <h2 class="abs heading">Shaking the Still</h2>
  <p class="abs" style="top:132px">The Shaking the Still workshop—an extension of the documentary of the same name—is an experiential process to transform participants into disturbers of the status quo within themselves, to enhance their relationships with others, and to change the environments in which they exist—and ultimately society—for the better.</p>
  <p class="abs" style="top:250px">This workshop experience challenges us all to understand the narratives we live within, to look at our current roles in society, and to decide what role we will play to create a more humane, just and peaceful world, for all. It all starts with our willingness to disturb the “peace” of the status quo.</p>
</section>

<section class="abs community" role="img" aria-label="Faded photo of a facilitator speaking to a seated group">
  <h2 class="abs heading">In Your Community</h2>
  <p class="abs">Bring ELsewhen or the Shaking the Still workshop to your community. We would love to hear from you. Please fill out the brief form here (link to In Your Community page)</p>
  <form class="abs contact-form">
    <div class="field">Your Name</div>
    <div class="field">Email address</div>
    <div class="field">Phone</div>
    <div class="field message">Message</div>
    <div class="send">Send</div>
  </form>
</section>

<footer class="abs footer">
  <div class="abs brand"><span class="brand-mark"></span>ELSEWHEN</div>
  <div class="abs footer-col" style="left:394px">
    <h3>Quick links</h3>
    <a>About Us</a><a>Workshops</a><a>ELsewhen Projects</a><a>Films</a>
  </div>
  <div class="abs footer-col" style="left:574px">
    <h3>Resources</h3>
    <a>Store &amp; Resources</a><a>Community</a><a>Contact Us</a>
  </div>
  <div class="abs footer-col" style="left:773px">
    <h3>Follow us</h3>
    <div class="social" aria-label="Social links"><span></span><span></span><span></span><span></span></div>
  </div>
</footer>
<div class="abs base">© 2018 Company Name. All right reserved</div>

</body>
</html>
```